Professional and creative business card design for recruiting service providers

Our company supports German medium-sized companies in filling vacancies promptly. For this we use social media marketing and bring our customers into the visibility.

We want a professional but also creative design for our business cards.

Please look at lindqvar-staff.de to get an impression of our CI.

Target Market(s)

Small and medium-sized companies in Germany from the industry

Industry/Entity Type

Industrie, Handwerk

Contact Information for Business Card

Name, Position, Telefonnummer, Email, Website

Colors
EE7325
F08F49
F5BC92
FAE3D3
FDF4ED

Requirements
Must have
• A picture of the employee and in the style of www.lindqvar-staff.de

```html
<!DOCTYPE html>
<html lang="de">
<head>
<meta charset="utf-8">
<title>Lindqvar &amp; Staff – Visitenkarte</title>
<link href="https://fonts.googleapis.com/css2?family=Montserrat:wght@700;800&family=Arimo:wght@400&display=swap" rel="stylesheet">
<style>
  :root {
    --brand-orange: #EE7325;
    --brand-orange-light: #F08F49;
    --brand-peach: #F5BC92;
    --brand-cream: #FAE3D3;
    --brand-ivory: #FDF4ED;
    --ink: #111111;
    --card-white: #ffffff;
    --backdrop: #e9e9ea;
  }
  * { box-sizing: border-box; margin: 0; padding: 0; }
  html, body {
    width: 1200px; height: 900px; overflow: hidden;
    background: var(--backdrop);
  }
  .stage {
    position: relative; width: 1200px; height: 900px;
    display: flex; flex-direction: column; align-items: center;
    justify-content: center; gap: 40px;
  }
  .card {
    position: relative; width: 640px; height: 372px;
    border-radius: 30px; overflow: hidden;
    box-shadow: 0 10px 24px rgba(0,0,0,0.18);
  }

  /* Back side */
  .card-back {
    background: var(--brand-orange);
    display: flex; align-items: center; justify-content: center;
  }
  .brand-lockup { display: flex; align-items: center; gap: 22px; }
  .brand-square {
    width: 46px; height: 46px; background: var(--card-white);
  }
  .brand-name {
    font-family: "Montserrat", sans-serif; font-weight: 800;
    font-size: 40px; line-height: 1.02; letter-spacing: 2px;
    text-transform: uppercase; color: var(--card-white);
  }

  /* Front side */
  .card-front { background: var(--card-white); }
  .front-info {
    position: absolute; left: 44px; top: 50px; width: 360px;
  }
  .card-front .brand-square { background: var(--brand-orange); }
  .card-front .brand-name { color: var(--ink); font-size: 34px; }
  .person-name {
    margin-top: 58px;
    font-family: "Montserrat", sans-serif; font-weight: 800;
    font-size: 27px; letter-spacing: 1px; text-transform: uppercase;
    color: var(--brand-orange);
  }
  .person-role {
    font-family: "Arimo", sans-serif; font-size: 19px;
    color: var(--ink); margin-top: 2px;
  }
  .contact-list { list-style: none; margin-top: 22px; }
  .contact-item {
    display: flex; align-items: center; gap: 10px;
    font-family: "Arimo", sans-serif; font-size: 18px;
    color: var(--ink); line-height: 1.5;
  }
  .contact-item svg { width: 18px; height: 18px; flex: none; }
  .accent { color: var(--brand-orange); }
  .employee-photo {
    position: absolute; right: 0; top: 0; width: 250px; height: 100%;
    background: linear-gradient(180deg, #ffffff 0%, #f2e6df 22%, #c99b82 40%, #4a4a4f 62%, #3a3a3e 100%);
  }
</style>
</head>
<body>
<main class="stage">
  <section class="card card-back">
    <div class="brand-lockup">
      <div class="brand-square"></div>
      <div class="brand-name">Lindqvar<br>&amp; Staff</div>
    </div>
  </section>

  <section class="card card-front">
    <div class="front-info">
      <div class="brand-lockup">
        <div class="brand-square"></div>
        <div class="brand-name">Lindqvar<br>&amp; Staff</div>
      </div>
      <h1 class="person-name">Mats Berendt</h1>
      <p class="person-role">Managing Director</p>
      <ul class="contact-list">
        <li class="contact-item">
          <svg viewBox="0 0 24 24"><path fill="#EE7325" d="M6.6 10.8a15.1 15.1 0 0 0 6.6 6.6l2.2-2.2a1 1 0 0 1 1-.25 11.4 11.4 0 0 0 3.6.57 1 1 0 0 1 1 1V20a1 1 0 0 1-1 1A17 17 0 0 1 3 4a1 1 0 0 1 1-1h3.5a1 1 0 0 1 1 1c0 1.25.2 2.45.57 3.6a1 1 0 0 1-.25 1z"/></svg>
          030-555 018 247
        </li>
        <li class="contact-item">
          <svg viewBox="0 0 24 24"><rect x="2" y="5" width="20" height="14" rx="1" fill="#EE7325"/><path d="M3 6l9 7 9-7" fill="none" stroke="#fff" stroke-width="1.8"/></svg>
          kontakt@lindqvar-staff.de
        </li>
        <li class="contact-item">
          <svg viewBox="0 0 24 24" fill="none" stroke="#EE7325" stroke-width="2"><circle cx="12" cy="12" r="9"/><path d="M3 12h18M12 3c3 3 3 15 0 18M12 3c-3 3-3 15 0 18"/></svg>
          <span>www.<span class="accent">lindqvar-staff</span>.de</span>
        </li>
      </ul>
    </div>
    <div class="employee-photo" role="img" aria-label="Portraitfoto des Mitarbeiters in dunklem Sakko und weißem Hemd"></div>
  </section>
</main>
</body>
</html>
```